Flyer-Design für Tauchunternehmen im südlichen Ägypten
Zielgruppe
Wir sind ein Tauchunternehmen im südlichen Ägypten, mit dem Hauptaugenmerk auf unser Tauchcenter und Meroka.
Aufgabenstellung
Es ist mir bewusst, dass es viel Content ist. Dieser kann ggf. auch angepasst werden. Der Flyer sollte in einem gängigen Format gedruckt werden können. Lieber mehrseitig, all flächenmässig zu gross.
Die beiden erwähnten Boote gehören unbedingt zu Meroka.
Die Zip Dateien sind auf die Themen abgestimmt, resp. das allgemeine Diving kann beliebig eingesetzt werden. Je ein Exemplar in Deutsch und Englisch wäre super. Beide Texte liegen vor.
Velora Diving Safari - Entdecke das Rote Meer
Wir zeigen euch unser tolles, vielfältiges zu Hause mit den schönsten Tauchplätzen.
Ob ihr erfahrene Taucher seid oder gerade erst euer Tauchabenteuer begonnen habt, erlebt mit uns die Schönheit der Unterwasserwelt mit ihren vielfältigen Korallen und Fischen.
Entfliehe mit uns dem Alltag.
Wir freuen uns, dich bei uns begrüssen zu dürfen!
Team Velora Diving Safari
Tarek & Petra
…..and into the ocean we go, to lose our mind and find our soul
Velora Diving Safari - Discover the Red Sea
We show you our great, diverse home with the most beautiful dive sites.
Whether you are an experienced diver or just starting your diving adventure, discover with us the beauty of the underwater world with its varied corals and fish.
Escape the daily routine with us.
We look forward to welcoming you!
.....and into the ocean we go, to lose our mind and find our soul
Tauchcenter
Wir sind im Hotel Belvano, südlich von El Quseir zu Hause. Von hier aus starten wir täglich zum Tauchen und Schnorcheln am Hausriff, vom Strand an die umliegenden Riffe und unseren Tagesbooten ab Port Ghalib und Hamata. Unser Team begleitet dich professionell bei deinen ersten Atemzügen unter Wasser, bildet dich nach QRX und BEMO-Standard aus oder führt dich sicher entlang der Tauchplätze.
Wir offerieren attraktive Arrangements mit Hotel und Tauchen..

```html
<!DOCTYPE html>
<html lang="en">
<head>
<meta charset="utf-8">
<title>Velora Diving Safari – Trifold Flyer</title>
<link rel="stylesheet" href="https://fonts.googleapis.com/css2?family=Poppins:wght@400;600;700&display=swap">
<style>
:root{
  --navy:#0c2b55;
  --blue:#1466c9;
  --sky:#3f8fe2;
  --pale:#9fc7f2;
  --white:#ffffff;
  --ink:#1d2733;
  --red:#d62828;
  --bg:#d9d9d9;
}
*{margin:0;padding:0;box-sizing:border-box}
html,body{width:1148px;height:1200px;overflow:hidden;background:var(--bg)}
body{font-family:"Poppins",sans-serif;color:var(--ink);position:relative}
.sheet{position:absolute;left:174px;width:800px;height:570px;background:var(--white);overflow:hidden;box-shadow:0 2px 8px rgba(0,0,0,.18)}
.sheet--inside{top:20px}
.sheet--outside{top:610px}
.abs{position:absolute}
.wave{position:absolute;display:block}
.heading{font-size:10px;font-weight:700;color:var(--ink);margin-bottom:6px}
.body{font-size:6.7px;line-height:1.6}
.block{position:absolute}
.photo{position:absolute}
.band{position:absolute;background:var(--navy)}
.banner{left:270px;top:15px;width:530px;height:37px;background:var(--navy);color:var(--white);font-size:10.5px;font-weight:700;display:flex;align-items:center;justify-content:center}
.on-dark{color:var(--white)}
.tagline{font-size:8.5px;font-weight:700;text-align:center}
.logo{display:flex;flex-direction:column;align-items:center;gap:8px}
.logo__dot{width:46px;height:46px;border-radius:50%;background:var(--navy)}
.logo__name{font-size:13px;font-weight:600;color:var(--navy);text-align:center;line-height:1.2}
.title{font-size:9.6px;font-weight:700;color:var(--navy)}
.contact{font-size:6.7px;line-height:1.6;color:var(--white)}
.social{display:flex;align-items:center;gap:8px;font-size:6.7px;color:var(--white);margin-bottom:7px}
.social__mark{width:13px;height:13px;border:1.2px solid var(--white);border-radius:2px}
.quote{font-style:italic}
</style>
</head>
<body>

<!-- Inside spread -->
<section class="sheet sheet--inside">
  <svg class="wave" style="left:0;top:0" width="800" height="60" viewBox="0 0 800 60" aria-hidden="true">
    <path d="M0 0H800V8C700 30 600 4 520 14 430 26 360 6 270 10 180 14 90 40 0 30Z" fill="var(--blue)"/>
    <path d="M0 30C90 40 180 14 270 10 200 22 120 44 0 46Z" fill="var(--sky)"/>
    <path d="M270 10C360 6 430 26 520 14 440 30 360 16 270 18Z" fill="var(--pale)"/>
  </svg>

  <div class="banner abs">Our boats, Salwan and Coralis 1, fully adapted to the needs of divers and snorkelers.</div>

  <div class="block" style="left:20px;top:60px;width:236px">
    <div class="heading">Daily boat</div>
    <p class="body">Enjoy a day at sea, diving and snorkeling in Marsa Mubarak. If you're lucky, you'll see the dugong and the big turtles. Snorkel in Meroka with the dolphins and along the islands of Hamata.</p>
  </div>
  <div class="block" style="left:20px;top:135px;width:236px">
    <div class="heading">Liveaboards</div>
    <p class="body">Experience a fantastic week on the Red Sea and explore some of the most stunning and colourful dive sites in the world. Find your favourite sites on our North Tour, South Tour or Deep South.</p>
  </div>

  <div class="photo" role="img" aria-label="White motor yacht Salwan on calm blue sea" style="left:281px;top:58px;width:240px;height:142px;background:linear-gradient(180deg,#b8cde0 0%,#dfe7ee 50%,#1c4f86 62%,#0f3560 100%)"></div>
  <div class="photo" role="img" aria-label="White motor yacht Coralis 1 at anchor" style="left:541px;top:58px;width:240px;height:142px;background:linear-gradient(180deg,#5a93cf 0%,#a9c9ea 50%,#1b5aa0 62%,#0d3a73 100%)"></div>

  <div class="band" style="left:0;top:202px;width:800px;height:163px"></div>
  <div class="photo" role="img" aria-label="Two divers underwater in blue water" style="left:18px;top:211px;width:238px;height:143px;background:radial-gradient(ellipse at 50% 20%,#4fa7e8,#1463b4 60%,#0a3b78)"></div>
  <div class="photo" role="img" aria-label="Boat saloon with blue sofas and warm lighting" style="left:281px;top:211px;width:240px;height:143px;background:linear-gradient(180deg,#c89a4a 0%,#5e4630 40%,#2b3b5c 70%,#1f2a44 100%)"></div>
  <div class="photo" role="img" aria-label="Long dining room on board with wooden panels" style="left:541px;top:211px;width:240px;height:143px;background:linear-gradient(180deg,#3b2418 0%,#7a4a2c 45%,#4a3a32 75%,#2a1f1a 100%)"></div>

  <div class="block" style="left:20px;top:380px;width:236px">
    <div class="heading">Full charter</div>
    <p class="body">Are you a larger group of divers or a dive club and want to be among yourselves on the boat? Then a full charter may be the best option.<br>Let us know your ideas, conditions, wishes and diving experience. We will plan an individual full charter considering your details and the conditions at hand.</p>
  </div>
  <div class="block" style="left:20px;top:488px;width:236px">
    <div class="heading">Diving courses</div>
    <p class="body">Learn to dive with our passionate instructors. As a partner of BEMO and QRX we train you in all levels from Scuba Diver to Dive Master. The courses can also be done during a liveaboard, depending on the conditions.</p>
  </div>

  <div class="block" style="left:281px;top:380px;width:240px">
    <div class="heading">Salwan</div>
    <p class="body">MY Salwan was built in 2019.<br>With a length of 30 metres and a beam of 8 metres, the steel-constructed boat comfortably accommodates 18 guests. 5 twin bed cabins and 2 double bed cabins are located on the lower deck and 2 single bed cabins on the upper deck.</p>
  </div>
  <div class="block" style="left:541px;top:380px;width:245px">
    <div class="heading">Coralis 1</div>
    <p class="body">MY Coralis 1 was built in 2021.<br>With a length of 32 metres and a beam of 8 metres, the steel-constructed boat comfortably accommodates 24 guests. 8 cabins with twin beds are located on the lower deck and 4 cabins on the upper deck.</p>
  </div>

  <div class="band" style="left:270px;top:493px;width:530px;height:77px"></div>
  <svg class="wave" style="left:270px;top:470px" width="530" height="100" viewBox="0 0 530 100" aria-hidden="true">
    <path d="M330 100C400 80 440 40 530 20V100Z" fill="var(--blue)"/>
    <path d="M400 100C450 84 490 60 530 50V100Z" fill="var(--sky)"/>
    <path d="M300 23H530V0C470 6 420 20 380 23Z" fill="var(--white)"/>
  </svg>
  <p class="body on-dark abs" style="left:282px;top:502px;width:420px">The restaurant on the main deck serves 3 buffets a day, and the spacious dive deck is where you get ready for adventure.<br>On the top deck, there is plenty of shaded seating and a bar for socialising and relaxing.<br>On the top deck, comfortable loungers await, ideal for enjoying the sun or watching the stars.</p>
</section>

<!-- Outside spread -->
<section class="sheet sheet--outside">
  <svg class="wave" style="left:0;top:0" width="267" height="60" viewBox="0 0 267 60" aria-hidden="true">
    <path d="M0 0H267V6C200 24 120 8 60 20 30 26 10 40 0 60Z" fill="var(--blue)"/>
    <path d="M0 60C10 40 30 26 60 20 30 34 12 46 6 60Z" fill="var(--sky)"/>
    <path d="M267 6C200 24 120 8 60 20 120 14 200 30 267 16Z" fill="var(--pale)"/>
  </svg>

  <div class="block" style="left:18px;top:30px;width:240px">
    <div class="heading">Full charter</div>
    <p class="body">Spend a week on a full charter at Meroka and/or Fury Shoals. Snorkel, dive, enjoy the time. Our boats offer plenty of space for rest, meditation or yoga. The region is perfect for the whole family. We look forward to seeing you and having an unforgettable time</p>
  </div>
  <div class="block" style="left:18px;top:150px;width:240px">
    <div class="heading">Mini Safari</div>
    <p class="body">Two nights at sea, ideal for snorkeling and diving at various locations in Fury Shoals.</p>
  </div>
  <div class="block" style="left:18px;top:225px;width:240px">
    <div class="heading">Overnight</div>
    <p class="body">Take a short break. Enjoy the sun, the stars and the sea. Experience the beauty of Meroka and spend a night on the boat. Explore the colourful reefs during your dives, or swim and snorkel with the dolphins and let them touch your soul.</p>
  </div>
  <div class="block" style="left:18px;top:317px;width:240px">
    <div class="heading">Daily boat</div>
    <p class="body">Sail to Meroka for a day. Swim and snorkel with the dolphins, enjoy a delicious lunch and go snorkeling again.</p>
  </div>
  <p class="tagline abs" style="left:0;top:372px;width:267px">Tours start and end at Hamata harbour.</p>
  <div class="photo" role="img" aria-label="Blue and white dive centre hut on the beach" style="left:0;top:393px;width:267px;height:177px;background:linear-gradient(180deg,#3f8be0 0%,#8cc0ef 35%,#1d6bc0 55%,#2a4d80 80%,#c9b79a 100%)"></div>

  <div class="photo" role="img" aria-label="Pod of dolphins swimming in deep blue water" style="left:267px;top:0;width:533px;height:224px;background:radial-gradient(ellipse at 45% 25%,#3ea2e6,#0f6cc0 55%,#063b7a)"></div>

  <div class="band" style="left:267px;top:224px;width:262px;height:346px"></div>
  <div class="block" style="left:275px;top:231px;width:250px">
    <div class="heading on-dark">Diving Centre</div>
    <p class="body on-dark">We are based at the Hotel Belvano, south of El Quseir. From here we depart daily for diving and snorkeling along the house reef, from the beach to the surrounding reefs and our daily boats from Port Ghalib and Hamata. Our team will accompany you professionally during your first breaths under water, train you according to QRX and BEMO standards or guide you safely along the dive sites.<br>We offer attractive packages with hotel and diving.</p>
  </div>
  <div class="photo" role="img" aria-label="Aerial view of hotel resort with pools by the sea" style="left:272px;top:352px;width:252px;height:128px;background:linear-gradient(180deg,#3d7fcf 0%,#6ea6dc 18%,#7b8a6e 40%,#4e9ec6 65%,#b49a78 100%)"></div>
  <div class="contact abs" style="left:275px;top:493px">Tarek +20 100 000 4821<br>Petra +41 79 000 31 58</div>
  <div class="contact abs" style="left:275px;top:532px">www.veloradivingsafari.com<br>info@veloradivingsafari.com</div>
  <div class="abs" style="left:417px;top:492px">
    <div class="social"><span class="social__mark"></span>velora_diving_safari</div>
    <div class="social"><span class="social__mark"></span>veloradiving.20</div>
    <div class="social"><span class="social__mark"></span>Velora Diving Safari</div>
  </div>

  <div class="logo abs" style="left:529px;top:240px;width:271px">
    <span class="logo__dot"></span>
    <span class="logo__name">Velora Diving Safari</span>
  </div>
  <div class="title abs" style="left:535px;top:350px;width:265px;text-align:center">Velora Diving Safari - Discover the Red Sea</div>
  <div class="block" style="left:546px;top:372px;width:240px">
    <p class="body">We show you our great, diverse home with the most beautiful dive sites. Whether you are an experienced diver or just starting your diving adventure, discover with us the beauty of the underwater world with its varied corals and fish.<br>Escape the daily routine with us.</p>
    <p class="body" style="margin-top:8px">We look forward to welcoming you!</p>
    <p class="body" style="margin-top:12px">Team Velora Diving Safari<br>Tarek &amp; Petra<br><span class="quote">…and into the ocean we go, to lose our mind and find our soul</span></p>
  </div>
  <svg class="wave" style="left:529px;top:470px" width="271" height="100" viewBox="0 0 271 100" aria-hidden="true">
    <path d="M0 100C80 90 170 70 271 0V100Z" fill="var(--blue)"/>
    <path d="M0 100C90 88 180 62 271 20V40C190 80 100 96 0 100Z" fill="var(--pale)"/>
    <path d="M60 100C140 92 210 70 271 50V100Z" fill="var(--sky)"/>
  </svg>
</section>

</body>
</html>
```